Dalvick's Business Card

I need some designs for a new business card including the new logo attached. An old example of our business card is also attached to show all the data that should be included on the new design.
**I added some more examples someone had mocked up**

Contact Information for Business Card

Should include all info on other examples uploaded.

```html
<!DOCTYPE html>
<html lang="en">
<head>
<meta charset="utf-8">
<title>Dalvick's Business Card</title>
<link rel="stylesheet" href="https://fonts.googleapis.com/css2?family=Montserrat:wght@400;600;800&family=Poppins:wght@400;500&display=swap">
<style>
  :root {
    --bg: #c9c9c9;
    --brand-blue: #1473c4;
    --brand-red: #e81f2b;
    --grad-blue: #0f6bbf;
    --grad-purple: #6a4a83;
    --grad-red: #ee1d2a;
    --card-black: #050505;
    --band-black: #111111;
    --white: #ffffff;
  }
  * { margin: 0; padding: 0; box-sizing: border-box; }
  html, body { width: 1200px; height: 900px; overflow: hidden; }
  body {
    background: var(--bg);
    font-family: "Montserrat", Arial, sans-serif;
    position: relative;
  }
  .card {
    position: absolute;
    left: 290px;
    width: 620px;
    height: 354px;
    border-radius: 26px;
    overflow: hidden;
    box-shadow: 0 8px 22px rgba(0,0,0,0.25);
  }
  /* Front */
  .card-front {
    top: 60px;
    background: linear-gradient(35deg, var(--grad-blue) 0%, var(--grad-purple) 50%, var(--grad-red) 100%);
    color: var(--white);
  }
  .front-decoration {
    position: absolute;
    right: -60px; top: -40px;
    width: 380px; height: 380px;
    border-radius: 50%;
    background: rgba(232, 31, 43, 0.28);
  }
  .front-content {
    position: absolute;
    left: 70px; top: 92px;
    right: 40px;
    text-align: center;
  }
  .brand-lockup {
    display: flex;
    align-items: center;
    justify-content: center;
    gap: 16px;
  }
  .brand-dot {
    width: 56px; height: 56px;
    border: 4px solid var(--white);
    border-radius: 50%;
  }
  .brand-text { text-align: left; }
  .brand-name {
    font-weight: 800;
    font-size: 54px;
    letter-spacing: 2px;
    line-height: 1;
  }
  .brand-tagline {
    font-weight: 600;
    font-size: 12.5px;
    letter-spacing: 1px;
    margin-top: 4px;
  }
  .service-area {
    font-size: 19px;
    font-weight: 400;
    margin-top: 26px;
    letter-spacing: 0.5px;
  }
  .call-to-action {
    font-weight: 800;
    font-size: 19px;
    line-height: 1.25;
    letter-spacing: 0.5px;
    margin-top: 22px;
  }
  /* Back */
  .card-back {
    top: 476px;
    background: var(--card-black);
  }
  .back-band {
    position: absolute;
    left: -50px; right: -50px;
    top: 140px;
    height: 90px;
    background: var(--band-black);
    transform: rotate(-12deg);
  }
  .back-decoration {
    position: absolute;
    right: -40px; top: 40px;
    width: 300px; height: 300px;
    border-radius: 50%;
    border: 14px solid var(--brand-red);
    border-top-color: var(--brand-blue);
    border-right-color: var(--brand-blue);
  }
  .back-content {
    position: absolute;
    left: 44px; top: 54px;
  }
  .back-name {
    color: var(--brand-blue);
    font-weight: 800;
    font-size: 50px;
    letter-spacing: 2px;
    line-height: 1;
  }
  .back-tagline {
    color: var(--brand-red);
    font-weight: 600;
    font-size: 12px;
    letter-spacing: 1px;
    margin-top: 4px;
  }
  .credentials {
    margin-top: 28px;
    font-weight: 800;
    font-size: 19px;
    line-height: 1.2;
  }
  .credentials .licensed { color: var(--brand-blue); }
  .credentials .family { color: var(--brand-red); }
  .contact-person {
    margin-top: 32px;
    color: var(--brand-blue);
    font-weight: 800;
    font-size: 26px;
    letter-spacing: 1px;
  }
  .contact-list { list-style: none; margin-top: 8px; }
  .contact-list li {
    display: flex;
    align-items: center;
    gap: 10px;
    color: var(--brand-red);
    font-family: "Poppins", Arial, sans-serif;
    font-size: 19px;
    line-height: 1.35;
  }
  .contact-icon { width: 20px; height: 20px; flex: none; }
</style>
</head>
<body>

<section class="card card-front">
  <div class="front-decoration" role="img" aria-label="Faint brand mark decoration"></div>
  <div class="front-content">
    <div class="brand-lockup">
      <span class="brand-dot"></span>
      <div class="brand-text">
        <div class="brand-name">DALVICK'S</div>
        <div class="brand-tagline">AIR CONDITIONING &amp; HEATING SERVICE</div>
      </div>
    </div>
    <p class="service-area">Serves Maple Falls, IA &amp; Surrounding Areas</p>
    <p class="call-to-action">CALL TODAY FOR ALL YOUR HVAC,<br>REFRIGERATION &amp; PLUMBING NEEDS</p>
  </div>
</section>

<section class="card card-back">
  <div class="back-band"></div>
  <div class="back-decoration" role="img" aria-label="Large brand mark decoration"></div>
  <div class="back-content">
    <div class="back-name">DALVICK'S</div>
    <div class="back-tagline">AIR CONDITIONING &amp; HEATING SERVICE</div>
    <p class="credentials">
      <span class="licensed">LICENSED &amp; INSURED</span><br>
      <span class="family">FAMILY OWNED &amp; OPERATED</span>
    </p>
    <p class="contact-person">MARCUS DALVICK</p>
    <ul class="contact-list">
      <li>
        <svg class="contact-icon" viewBox="0 0 24 24" aria-hidden="true">
          <path fill="#1473c4" d="M6.6 10.8a15.1 15.1 0 0 0 6.6 6.6l2.2-2.2c.3-.3.7-.4 1-.2 1.1.4 2.3.6 3.6.6.6 0 1 .4 1 1V20c0 .6-.4 1-1 1A17 17 0 0 1 3 4c0-.6.4-1 1-1h3.5c.6 0 1 .4 1 1 0 1.3.2 2.5.6 3.6.1.3 0 .7-.2 1z"/>
        </svg>
        555.014.2290
      </li>
      <li>
        <svg class="contact-icon" viewBox="0 0 24 24" aria-hidden="true">
          <rect x="2" y="5" width="20" height="14" fill="#1473c4"/>
          <path d="M2 5l10 8 10-8" fill="none" stroke="#050505" stroke-width="1.6"/>
        </svg>
        service@dalvickhvac.com
      </li>
    </ul>
  </div>
</section>

</body>
</html>
```